Lumra Learning Web Design Project

Who We are:
Lumra Learning is education information portal/ magazine, providing information about the Chinese and International education markets. Our aim is to help school principals improve there curriculum, and parents in understanding this curriculum.

Project Brief:
The site will include education news updates, educational services, curriculum developments and overseas study. We hope the site represents the cross cultural bridge between the west and east. The site will cover both the Sciences and Arts.

Note:
The logo design competition is also underway so we only need the website design

What We want:
This competition is for Design only no coding!
Design a home page based on Template 1,2 or 3. I only need to select one.
The design of an article page.

Optional
Design a Parvex Shutters metro style splash page.

Sites We like:
http://www.qv.com.cn/tonguebridge/default.aspx
http://www.dailyuniversitybulletin.co.uk/
http://kptz.sinocraftlearn.net/

Template Explanations:
Template 1-
The main information has a dynamic sliding category view that when clicked displays the relevant info.
In addition to the main upper menu it also has a left hand sliding menu that pops out on click or gesture

Template 2-
Has limited number of Articles most of the menus are drop downs from the top menu

Template 3-
No Top menu

Target Market(s)

Teachers, principals and parents

Industry/Entity Type

Education

Requirements
Should not have
• kindergarten preschool feel

```html
<!DOCTYPE html>
<html lang="en">
<head>
<meta charset="utf-8">
<title>Lumra Learning</title>
<link rel="stylesheet" href="https://fonts.googleapis.com/css2?family=Source+Sans+3:wght@400;600;700&display=swap">
<style>
:root{
  --red:#dc2318;
  --red-dark:#c01a12;
  --blue:#0d5aa0;
  --blue-dark:#0a4680;
  --blue-line:#2f74b5;
  --navy:#1a4f80;
  --sky:#cde9f8;
  --footer-dark:#2b2b2b;
  --white:#ffffff;
}
*{box-sizing:border-box;margin:0;padding:0}
html,body{width:1200px;height:1080px;overflow:hidden;background:var(--white)}
body{position:relative;font-family:"Source Sans 3",Arial,sans-serif;color:var(--white)}
a{color:inherit;text-decoration:none}
.top-strip{position:absolute;left:0;top:0;width:1200px;height:5px;background:var(--red)}

.brand{position:absolute;left:118px;top:95px;display:flex;align-items:center;gap:10px}
.brand-dot{width:26px;height:26px;border-radius:50%;background:var(--red)}
.brand-name{font-size:25px;font-weight:700;color:var(--navy);letter-spacing:.3px}

.search{position:absolute;left:779px;top:60px;width:300px;height:35px;border:1px solid #cfcfcf;background:var(--white)}
.search svg{position:absolute;right:10px;top:9px}

.side-nav{position:absolute;left:119px;top:161px;width:150px;height:333px;background:linear-gradient(90deg,var(--blue-dark),var(--blue));border-bottom:2px solid var(--blue-dark)}
.side-nav a{display:block;height:47.5px;line-height:44px;padding-left:30px;font-size:14px;font-weight:600;border-bottom:1px solid var(--blue-line)}
.side-nav a:last-child{border-bottom:none}

.social{position:absolute;left:119px;top:503px;width:150px;height:365px;background:linear-gradient(90deg,var(--blue-dark),var(--blue))}
.social a{display:flex;align-items:center;height:60.8px;padding-left:12px;gap:11px;font-size:14px;font-weight:600;border-bottom:1px solid var(--blue-line)}
.social a:last-child{border-bottom:none}
.social .dot{width:36px;height:36px;border-radius:50%;background:var(--white);display:flex;align-items:center;justify-content:center}
.social .dot i{display:block;width:28px;height:28px;border-radius:50%}

.main-nav{position:absolute;left:280px;top:160px;width:800px;height:40px;background:var(--red);display:flex;border-bottom:1px solid var(--red-dark)}
.main-nav a{height:40px;line-height:40px;text-align:center;font-size:15px;font-weight:600;border-right:1px solid var(--red-dark)}
.main-nav a:last-child{border-right:none}

.hero{position:absolute;left:280px;top:211px;width:590px;height:260px;background:linear-gradient(120deg,#7d8894 0%,#c9c3bb 35%,#e8ddd0 60%,#a9b8c8 100%)}
.hero-dots{position:absolute;right:10px;bottom:14px;display:flex;gap:5px}
.hero-dots span{width:10px;height:10px;border-radius:50%;background:#9a9a9a;border:1px solid #fff}
.hero-dots span:first-child{background:#333}

.categories{position:absolute;left:280px;top:480px;width:590px;height:388px;border:1px solid #e2e2e2;border-top:none}
.categories h2{height:40px;line-height:40px;padding-left:12px;background:linear-gradient(var(--blue),var(--blue-dark));font-size:18px;font-weight:600;margin:0 -1px}
.cat-grid{position:absolute;left:9px;top:48px;display:grid;grid-template-columns:280px 280px;column-gap:10px;row-gap:10px}
.cat-photo{height:91px;margin-bottom:-10px}
.photo-a{background:linear-gradient(100deg,#d9d2cc,#8f7a6e 40%,#c8c2bc)}
.photo-b{background:linear-gradient(100deg,#4b3b33,#e0c39a 45%,#7a6a60)}
.cat-grid a{display:block;height:40px;line-height:36px;padding-left:8px;font-size:14px;font-weight:600;background:linear-gradient(var(--blue),var(--blue-dark));border:1px solid var(--blue-dark)}

.ad-frame{position:absolute;left:880px;top:211px;width:200px;height:657px;background:var(--red)}
.ad{position:absolute;left:19px;top:30px;width:162px;height:600px;background:linear-gradient(var(--sky),#e7f5fd)}

.footer{position:absolute;left:0;top:890px;width:1200px;height:156px;background:var(--red)}
.footer ul{position:absolute;top:20px;list-style:none}
.footer li{height:24px;font-size:13.5px;font-weight:600}
.col-1{left:187px}.col-2{left:427px}.col-3{left:669px}.col-4{left:908px}
.legal{position:absolute;left:0;top:1046px;width:1200px;height:34px;background:var(--footer-dark);line-height:34px;text-align:center;font-size:13.5px;padding-right:57px}
</style>
</head>
<body>
<div class="top-strip"></div>

<header>
  <a class="brand" href="#"><span class="brand-dot"></span><span class="brand-name">Lumra Learning</span></a>
  <form class="search" role="search">
    <svg width="16" height="14" viewBox="0 0 16 14" aria-hidden="true"><circle cx="5" cy="5" r="3.6" fill="none" stroke="#dc2318" stroke-width="2"/><line x1="7.6" y1="7.6" x2="14" y2="13" stroke="#dc2318" stroke-width="2.4" stroke-linecap="round"/></svg>
  </form>
</header>

<nav class="side-nav">
  <a href="#">HOME</a><a href="#">ABOUT US</a><a href="#">BLOG</a><a href="#">COURSES</a><a href="#">BLOG</a><a href="#">TESTIMONIALS</a><a href="#">CONTATC US</a>
</nav>

<nav class="social">
  <a href="#"><span class="dot"><i style="background:#3b5a98"></i></span>facenote</a>
  <a href="#"><span class="dot"><i style="background:#26a6e2"></i></span>chirper</a>
  <a href="#"><span class="dot"><i style="background:#1479b8"></i></span>linkpro</a>
  <a href="#"><span class="dot"><i style="background:#d42a25"></i></span>glowplus</a>
  <a href="#"><span class="dot"><i style="background:#c8422c"></i></span>vidstream</a>
  <a href="#"><span class="dot"><i style="background:#f08a24"></i></span>RSS Feed</a>
</nav>

<nav class="main-nav">
  <a href="#" style="width:89px">HOME</a><a href="#" style="width:126px">ABOUT US</a><a href="#" style="width:94px">BLOG</a><a href="#" style="width:120px">COURSES</a><a href="#" style="width:92px">BLOG</a><a href="#" style="width:155px">TESTIMONIALS</a><a href="#" style="width:124px">CONTATC US</a>
</nav>

<section class="hero" role="img" aria-label="Photo of students seated at desks in a classroom listening to a teacher">
  <div class="hero-dots"><span></span><span></span><span></span></div>
</section>

<section class="categories">
  <h2>CATEGORIES</h2>
  <div class="cat-grid">
    <div class="cat-photo photo-a" role="img" aria-label="Photo of students working at laptops"></div>
    <div class="cat-photo photo-b" role="img" aria-label="Photo of a student reading in class"></div>
    <a href="#">Computer Science</a><a href="#">History</a>
    <a href="#">Accounting</a><a href="#">Drama</a>
    <a href="#">Asia</a><a href="#">Science</a>
    <a href="#">USA</a><a href="#">English</a>
    <a href="#">Commerce</a><a href="#">Computer Science</a>
  </div>
</section>

<aside class="ad-frame">
  <div class="ad" role="img" aria-label="Sidebar advertisement banner with a pale blue winter design"></div>
</aside>

<footer class="footer">
  <ul class="col-1"><li>Home</li><li>About Us</li><li>Subjects</li><li>My Courses</li><li>Contact Us</li></ul>
  <ul class="col-2"><li>Computer Science</li><li>Accounting</li><li>History</li><li>Drama</li><li>Asia</li></ul>
  <ul class="col-3"><li>Commerce</li><li>English</li><li>USA</li><li>Asia</li><li>Commerce</li></ul>
  <ul class="col-4"><li>Commerce</li><li>English</li><li>USA</li><li>Asia</li><li>Commerce</li></ul>
</footer>
<div class="legal">©2013 Lumra Learning &nbsp;| All Rihts Reserved.</div>
</body>
</html>
```